Business Card Design for a Software Startup

We'd like to have a business card design. We already have a logo. Basically what we need is a clean design with name, address, cellphone and phone numbers, e-mail and web site address (front) and a space on the back with our logo with the company name on the right side and some texts on the bottom.
We are a development and consulting company in Brazil with highly qualified team of professionals in Java, iOS and Android development and consulting.

Target Market(s)

CIO, IT managers of mid to big size companies

Industry/Entity Type

Business

```html
<!DOCTYPE html>
<html lang="en">
<head>
<meta charset="utf-8">
<title>VANTRO Business Card</title>
<link rel="stylesheet" href="https://fonts.googleapis.com/css2?family=Open+Sans:wght@400;600;700;800&display=swap">
<style>
  :root {
    --backdrop: #e4e5ea;
    --card: #ffffff;
    --navy: #0d3a64;
    --blue-deep: #1f5d98;
    --blue-mid: #1a78bd;
    --blue-light: #1ea7e4;
    --ink: #2b2b2b;
    --rule: #d4d6da;
  }
  * { margin: 0; padding: 0; box-sizing: border-box; }
  html, body { width: 1200px; height: 987px; overflow: hidden; }
  body {
    background: var(--backdrop);
    font-family: "Open Sans", Arial, sans-serif;
    position: relative;
  }
  .card {
    position: absolute;
    left: 230px;
    width: 740px;
    height: 423px;
    background: var(--card);
    border-radius: 34px;
    overflow: hidden;
    box-shadow: 0 6px 22px rgba(40, 50, 70, 0.18);
  }
  .card--front { top: 40px; }
  .card--back { top: 524px; }

  .card__art { position: absolute; inset: 0; width: 100%; height: 100%; }

  .brand {
    position: absolute;
    left: 48px;
    top: 118px;
    display: flex;
    align-items: center;
    gap: 16px;
  }
  .brand__mark {
    width: 34px;
    height: 34px;
    border-radius: 6px;
    background: var(--blue-mid);
  }
  .brand__name {
    font-weight: 800;
    font-size: 56px;
    letter-spacing: 1px;
    color: var(--navy);
    line-height: 1;
  }

  .divider {
    position: absolute;
    left: 262px;
    top: 190px;
    width: 1px;
    height: 170px;
    background: var(--rule);
  }

  .contact {
    position: absolute;
    left: 284px;
    top: 196px;
    list-style: none;
    color: var(--ink);
    font-size: 19px;
    line-height: 28px;
  }
  .contact__item { display: flex; align-items: center; gap: 9px; }
  .contact__icon { width: 15px; height: 15px; flex: none; }
  .address {
    position: absolute;
    left: 284px;
    top: 322px;
    color: var(--ink);
    font-size: 19px;
    line-height: 27px;
  }

  .person {
    position: absolute;
    right: 44px;
    top: 120px;
    text-align: right;
    color: #ffffff;
  }
  .person__name { font-weight: 700; font-size: 30px; line-height: 1.1; }
  .person__title { font-size: 20px; margin-top: 4px; }

  .back__name {
    position: absolute;
    left: 0; right: 0;
    top: 128px;
    text-align: center;
    font-weight: 800;
    font-size: 118px;
    letter-spacing: 4px;
    color: var(--navy);
    line-height: 1;
  }
  .back__web {
    position: absolute;
    left: 0; right: 0;
    top: 290px;
    text-align: center;
    font-size: 20px;
    letter-spacing: 6px;
    color: var(--ink);
  }
</style>
</head>
<body>

<section class="card card--front" aria-label="Front of card">
  <svg class="card__art" viewBox="0 0 740 423" aria-hidden="true">
    <defs>
      <linearGradient id="swoosh-fill" x1="0" y1="0" x2="0.4" y2="1">
        <stop offset="0" stop-color="#1ea7e4"/>
        <stop offset="0.45" stop-color="#1a78bd"/>
        <stop offset="1" stop-color="#255a92"/>
      </linearGradient>
    </defs>
    <path d="M 236 0 C 450 40 595 200 700 423 L 740 423 L 740 0 Z" fill="url(#swoosh-fill)"/>
    <path d="M 170 0 C 400 40 560 200 646 423 L 672 423 C 578 200 420 36 204 0 Z" fill="var(--navy)"/>
  </svg>

  <div class="brand">
    <span class="brand__mark"></span>
    <span class="brand__name">VANTRO</span>
  </div>

  <div class="divider"></div>

  <ul class="contact">
    <li class="contact__item">
      <svg class="contact__icon" viewBox="0 0 16 16"><circle cx="8" cy="8" r="7.5" fill="var(--blue-deep)"/><path d="M5 4.5 L6.6 4.2 L7.3 6.2 L6.3 7 C6.8 8.1 7.8 9.2 9 9.7 L9.8 8.7 L11.8 9.4 L11.5 11 C8 11.4 4.6 8 5 4.5 Z" fill="#fff"/></svg>
      <span>123-456-7890</span>
    </li>
    <li class="contact__item">
      <svg class="contact__icon" viewBox="0 0 16 16"><rect x="4" y="1" width="8" height="14" rx="1.5" fill="var(--blue-deep)"/><rect x="5.5" y="3" width="5" height="6" fill="#fff"/></svg>
      <span>456-085-4321</span>
    </li>
    <li class="contact__item">
      <svg class="contact__icon" viewBox="0 0 16 16"><rect x="1" y="3.5" width="14" height="9" rx="1" fill="var(--blue-deep)"/><path d="M1.5 4 L8 9 L14.5 4" fill="none" stroke="#fff" stroke-width="1.2"/></svg>
      <span>yourname@vantro.com</span>
    </li>
    <li class="contact__item">
      <svg class="contact__icon" viewBox="0 0 16 16"><circle cx="8" cy="8" r="7" fill="var(--blue-deep)"/><g fill="none" stroke="#fff" stroke-width="0.9"><ellipse cx="8" cy="8" rx="3" ry="7"/><path d="M1 8 H15 M2.5 4.5 H13.5 M2.5 11.5 H13.5"/></g></svg>
      <span>www.vantro.com</span>
    </li>
  </ul>

  <p class="address">Door No. Street Name<br>City Name, State, Zip Code</p>

  <div class="person">
    <p class="person__name">Your Name</p>
    <p class="person__title">Title</p>
  </div>
</section>

<section class="card card--back" aria-label="Back of card">
  <p class="back__name">VANTRO</p>
  <p class="back__web">www.vantro.com</p>
</section>

</body>
</html>
```